Business card for law firm

Need business card for new law firm. Think confident, authoritative, conservative, but not stuffy or old-fashioned.

Contact Information for Business Card

Content for card - logo (uploaded), plus the following:

Paul Whitcombe (larger font)
Managing Partner (larger font, but not as large as name)
Level 9, 7 Ferris Lane
Sydney NSW 2000
Main Tel 02 9364 2710
Direct Tel 02 8472 3159
Email paul@qvlegal.com.au
www.qvlegal.com.au

Letterhead design should include logo plus:
Level 9, 7 Ferris Lane
Sydney NSW 2000
Tel 02 8472 3159
www.qvlegal.com.au

```html
<!DOCTYPE html>
<html lang="en">
<head>
<meta charset="utf-8">
<title>Quayvale Lawyers – Business Card</title>
<link rel="stylesheet" href="https://fonts.googleapis.com/css2?family=Open+Sans:wght@400;600;700&display=swap">
<style>
  :root {
    --navy: #001d57;
    --ink: #111111;
    --paper: #ffffff;
    --backdrop: #d9dadc;
    --edge: #b9babd;
  }
  * { box-sizing: border-box; margin: 0; padding: 0; }
  html, body { width: 1200px; height: 1113px; overflow: hidden; }
  body {
    background: var(--backdrop);
    font-family: "Open Sans", Arial, sans-serif;
    position: relative;
  }
  .card {
    position: absolute;
    left: 165px;
    width: 870px;
    height: 470px;
    background: var(--paper);
    border-radius: 34px;
    border: 1px solid var(--edge);
    overflow: hidden;
  }
  .card--front { top: 60px; }
  .card--back { top: 585px; }

  .card__band { position: absolute; inset: 0; width: 100%; height: 100%; }

  .brand {
    position: absolute;
    left: 0; right: 0;
    text-align: center;
    color: var(--navy);
    font-weight: 600;
  }
  .brand__mark {
    display: block;
    margin: 0 auto;
    background: var(--navy);
  }
  .brand__name { display: block; letter-spacing: 2px; line-height: 1; }
  .brand__sub { display: block; letter-spacing: 14px; line-height: 1; padding-left: 14px; }

  .card--front .brand { top: 28px; left: 60px; }
  .card--front .brand__mark { width: 62px; height: 80px; margin-bottom: 16px; }
  .card--front .brand__name { font-size: 46px; }
  .card--front .brand__sub { font-size: 15px; margin-top: 8px; }

  .holder {
    position: absolute;
    top: 208px; left: 70px; right: 0;
    text-align: center;
  }
  .holder__name {
    color: var(--navy);
    font-weight: 700;
    font-size: 29px;
    line-height: 1.1;
  }
  .holder__role {
    color: var(--ink);
    font-size: 19px;
    line-height: 1.3;
  }

  .contact {
    position: absolute;
    top: 336px; left: 230px; right: 40px;
    color: var(--paper);
    font-size: 19px;
    line-height: 33px;
    text-align: center;
  }
  .contact__line { display: flex; justify-content: center; gap: 18px; white-space: nowrap; }
  .contact__item { display: inline-flex; align-items: center; gap: 6px; }
  .contact__icon { width: 16px; height: 16px; fill: none; stroke: var(--paper); stroke-width: 1.6; }

  .card--back .brand { top: 48px; }
  .card--back .brand__mark { width: 92px; height: 112px; margin-bottom: 40px; }
  .card--back .brand__name { font-size: 72px; }
  .card--back .brand__sub { font-size: 22px; margin-top: 10px; letter-spacing: 22px; padding-left: 22px; }

  .site {
    position: absolute;
    left: 0; right: 0; bottom: 62px;
    text-align: center;
    font-size: 26px;
    letter-spacing: 4px;
    color: var(--ink);
  }
  .site__key { color: var(--navy); font-weight: 700; }
</style>
</head>
<body>

<section class="card card--front" aria-label="Business card front">
  <svg class="card__band" viewBox="0 0 870 470" preserveAspectRatio="none" aria-hidden="true">
    <path d="M0,150 C200,255 420,292 640,302 C420,300 200,276 0,182 Z" fill="var(--ink)"/>
    <path d="M0,200 C180,290 380,318 560,318 C700,318 800,300 870,282 V470 H0 Z" fill="var(--navy)"/>
  </svg>

  <div class="brand">
    <span class="brand__mark"></span>
    <span class="brand__name">QUAYVALE</span>
    <span class="brand__sub">LAWYERS</span>
  </div>

  <div class="holder">
    <p class="holder__name">PAUL WHITCOMBE</p>
    <p class="holder__role">MANAGING PARTNER</p>
  </div>

  <div class="contact">
    <p class="contact__line">
      <span class="contact__item">
        <svg class="contact__icon" viewBox="0 0 16 16"><path d="M4 1.5 L6.5 4.5 L5 6.5 C6 8.5 7.5 10 9.5 11 L11.5 9.5 L14.5 12 L12.5 14.5 C7 14 2 9 1.5 3.5 Z"/></svg>
        02 9364 2710(Main)
      </span>
      <span class="contact__item">
        <svg class="contact__icon" viewBox="0 0 16 16"><path d="M4 1.5 L6.5 4.5 L5 6.5 C6 8.5 7.5 10 9.5 11 L11.5 9.5 L14.5 12 L12.5 14.5 C7 14 2 9 1.5 3.5 Z"/></svg>
        02 8472 3159(Direct)
      </span>
    </p>
    <p class="contact__line">
      <span class="contact__item">
        <svg class="contact__icon" viewBox="0 0 16 16"><rect x="1.5" y="3.5" width="13" height="9"/><path d="M1.5 3.5 L8 9 L14.5 3.5"/></svg>
        paul@qvlegal.com.au
      </span>
      <span class="contact__item">
        <svg class="contact__icon" viewBox="0 0 16 16"><circle cx="8" cy="8" r="6.5"/><ellipse cx="8" cy="8" rx="3" ry="6.5"/><path d="M1.5 8 H14.5"/></svg>
        www.qvlegal.com.au
      </span>
    </p>
    <p class="contact__line">Level 9, 7 Ferris Lane, Sydney NSW 2000</p>
  </div>
</section>

<section class="card card--back" aria-label="Business card back">
  <div class="brand">
    <span class="brand__mark"></span>
    <span class="brand__name">QUAYVALE</span>
    <span class="brand__sub">LAWYERS</span>
  </div>
  <p class="site">www.<span class="site__key">qvlegal</span>.com.au</p>
</section>

</body>
</html>
```